Redesign of business card for Cedar Ridge Mechanical

We are looking for a new design for our business cards for Cedar Ridge Mechanical. We are a plumbing & HVAC construction company, operating on the West Coast of Canada and USA. Logo attached.
Industry/Entity Type
Construction - Plumbing & HVAC
Contact Information for Business Card
Name, address, phone numbers, email, website address
Look and feel
Each slider illustrates characteristics of the customer's brand and the style your logo design should communicate.

```html
<!DOCTYPE html>
<html lang="en">
<head>
<meta charset="utf-8">
<title>Cedar Ridge Mechanical – Business Card</title>
<link href="https://fonts.googleapis.com/css2?family=Poppins:wght@300;400;700&display=swap" rel="stylesheet">
<style>
  :root {
    --page-bg: #232323;
    --card-bg: #1c1c1e;
    --ink: #ffffff;
    --ink-soft: #d9d9d9;
    --shadow: rgba(0,0,0,0.55);
  }
  * { margin: 0; padding: 0; box-sizing: border-box; }
  html, body { width: 1200px; height: 780px; overflow: hidden; }
  body {
    background: var(--page-bg);
    font-family: "Poppins", sans-serif;
    color: var(--ink);
    position: relative;
  }
  .card {
    position: absolute;
    top: 240px;
    width: 520px;
    height: 300px;
    background: var(--card-bg);
    border-radius: 6px;
    box-shadow: 0 18px 40px var(--shadow);
    overflow: hidden;
  }
  .card--front { left: 60px; }
  .card--back { left: 620px; }

  .brand {
    position: absolute;
    display: flex;
    align-items: center;
    gap: 10px;
    font-weight: 700;
    text-transform: uppercase;
    color: var(--ink);
    letter-spacing: 0.04em;
  }
  .brand__mark {
    border: 2px solid var(--ink);
    border-radius: 4px;
    flex: none;
  }
  .card--front .brand { top: 30px; left: 32px; font-size: 15px; line-height: 1.15; }
  .card--front .brand__mark { width: 34px; height: 34px; }

  .contact {
    position: absolute;
    left: 32px;
    top: 118px;
    font-size: 12.5px;
    font-weight: 300;
    line-height: 1.55;
    color: var(--ink-soft);
  }
  .contact__address { margin-bottom: 8px; }
  .contact__row { display: flex; align-items: center; gap: 8px; }
  .contact__row svg { width: 11px; height: 11px; fill: var(--ink); flex: none; }

  .person {
    position: absolute;
    right: 34px;
    top: 138px;
    text-align: right;
  }
  .person__name { font-size: 26px; line-height: 1.1; white-space: nowrap; }
  .person__first { font-weight: 700; }
  .person__last { font-weight: 300; }
  .person__title { font-size: 14px; font-weight: 300; margin-top: 2px; }
  .accent-bar {
    position: absolute;
    right: 0;
    top: 138px;
    width: 12px;
    height: 56px;
    background: var(--ink);
  }

  .card--back .brand {
    top: 50%;
    left: 50%;
    transform: translate(-50%, -50%);
    font-size: 24px;
    white-space: nowrap;
    color: #c9c9c9;
  }
</style>
</head>
<body>
  <section class="card card--front" aria-label="Business card front">
    <div class="brand">
      <span class="brand__mark"></span>
      <span class="brand__name">Cedar Ridge<br>Mechanical</span>
    </div>
    <div class="contact">
      <p class="contact__address">1840 Harbor Ln. Suite 310<br>Tacoma, WA 98402</p>
      <p class="contact__row">
        <svg viewBox="0 0 24 24" aria-hidden="true"><path d="M6.6 10.8a15 15 0 0 0 6.6 6.6l2.2-2.2c.3-.3.7-.4 1-.2 1.1.4 2.3.6 3.6.6.6 0 1 .4 1 1V20c0 .6-.4 1-1 1A17 17 0 0 1 3 4c0-.6.4-1 1-1h3.5c.6 0 1 .4 1 1 0 1.2.2 2.4.6 3.6.1.3 0 .7-.2 1z"/></svg>
        (253) 555-0147
      </p>
      <p class="contact__row">
        <svg viewBox="0 0 24 24" aria-hidden="true"><path d="M12 2a10 10 0 1 0 0 20 10 10 0 0 0 0-20zm0 2c1 0 2.3 2 2.8 5H9.2C9.7 6 11 4 12 4zm-8 8c0-.7.1-1.4.3-2h3c-.1.7-.1 1.3-.1 2s0 1.3.1 2h-3c-.2-.6-.3-1.3-.3-2zm8 8c-1 0-2.3-2-2.8-5h5.6c-.5 3-1.8 5-2.8 5zm3-7H9a13 13 0 0 1 0-2h6a13 13 0 0 1 0 2zm1.7 1h3c-.8 2-2.5 3.6-4.5 4.3.6-1.1 1.2-2.6 1.5-4.3zm0-4c-.3-1.7-.9-3.2-1.5-4.3 2 .7 3.7 2.3 4.5 4.3z"/></svg>
        info@cedarridgemech.com
      </p>
      <p class="contact__row">
        <svg viewBox="0 0 24 24" aria-hidden="true"><path d="M3 5h18c.6 0 1 .4 1 1v12c0 .6-.4 1-1 1H3c-.6 0-1-.4-1-1V6c0-.6.4-1 1-1zm9 7.5L4 7.3V17h16V7.3z"/></svg>
        www.cedarridgemech.com
      </p>
    </div>
    <div class="person">
      <p class="person__name"><span class="person__first">Marta</span> <span class="person__last">Kovalik</span></p>
      <p class="person__title">Founder &amp; CEO</p>
    </div>
    <span class="accent-bar" aria-hidden="true"></span>
  </section>

  <section class="card card--back" aria-label="Business card back">
    <div class="brand">
      <span class="brand__name">Cedar Ridge Mechanical</span>
    </div>
  </section>
</body>
</html>
```